Verodex business card

Business card for sustainable investment company called "Verodex". Verodex is an exchange platform selling carbon credits between buyers and sellers. Carbon Credits are an environmental commodity for reducing global carbon emissions.

the card should obviously have our logo and the theme should be sustainability/environment mixed with a trading platform.

Contact Information for Business Card

Logo, Name, Title, Phone, Email

Colors
0054AA
0677BA
7BADD7
CADEEF
E8F1F8
0094D4
00A9DD
6FCCEA
C7EBF8
E9F6FB
00AB8E
00BBA5
67D7C9
C6EFE9
E9F9F6
59FF00
82FF00
B8FF75
E3FFCB
F4FFEA

```html
<!DOCTYPE html>
<html lang="en">
<head>
<meta charset="utf-8">
<title>Verodex business card</title>
<link href="https://fonts.googleapis.com/css2?family=Montserrat:wght@400;500;700&display=swap" rel="stylesheet">
<style>
  :root {
    --backdrop: #3b3c3e;
    --paper: #ffffff;
    --navy: #172a53;
    --ink: #1b1f2a;
    --accent: #56a7d3;
    --accent-deep: #4a86c9;
    --tint: #eaf3f9;
  }
  * { margin: 0; padding: 0; box-sizing: border-box; }
  html, body {
    width: 1200px; height: 1059px; overflow: hidden;
    background: var(--backdrop);
    font-family: "Montserrat", sans-serif;
  }
  .canvas { position: relative; width: 1200px; height: 1059px; }
  .card { position: absolute; overflow: hidden; }
  .card-front {
    left: 256px; top: 100px; width: 688px; height: 391px;
    background: linear-gradient(90deg, var(--paper) 0%, var(--paper) 62%, var(--tint) 100%);
  }
  .card-back {
    left: 253px; top: 537px; width: 694px; height: 394px;
    background: var(--navy);
  }
  .brand { position: absolute; display: flex; align-items: center; }
  .brand-mark { display: block; background: var(--accent); }
  .brand-name { font-weight: 700; letter-spacing: 0.5px; line-height: 1; }
  .card-front .brand { left: 29px; top: 60px; gap: 16px; }
  .card-front .brand-mark { width: 56px; height: 56px; }
  .card-front .brand-name { font-size: 46px; color: var(--navy); }
  .card-back .brand { left: 0; right: 0; top: 160px; justify-content: center; gap: 24px; }
  .card-back .brand-mark { width: 84px; height: 84px; background: linear-gradient(90deg, #62c6dc, var(--accent-deep)); }
  .card-back .brand-name { font-size: 64px; color: var(--paper); }
  .accent-bar {
    position: absolute; left: 0; top: 172px; width: 16px; height: 42px;
    background: var(--accent);
  }
  .person { position: absolute; left: 29px; top: 169px; }
  .person-name { font-size: 27px; font-weight: 700; color: var(--navy); letter-spacing: 1px; line-height: 1.1; }
  .person-title { font-size: 18px; font-weight: 400; color: var(--ink); letter-spacing: 0.5px; line-height: 1.2; }
  .address {
    position: absolute; left: 29px; top: 233px;
    font-size: 16px; line-height: 22px; color: var(--ink); letter-spacing: 0.3px;
  }
  .contacts { position: absolute; left: 29px; top: 292px; list-style: none; }
  .contacts li {
    display: flex; align-items: center; gap: 8px; height: 26px;
    font-size: 16px; color: var(--ink); letter-spacing: 0.3px;
  }
  .contacts svg { width: 13px; height: 13px; fill: var(--accent); flex: none; }
</style>
</head>
<body>
<div class="canvas">
  <section class="card card-front">
    <div class="brand">
      <span class="brand-mark"></span>
      <span class="brand-name">VERODEX</span>
    </div>
    <span class="accent-bar"></span>
    <div class="person">
      <p class="person-name">DANA HOLLOWAY</p>
      <p class="person-title">MANAGER</p>
    </div>
    <p class="address">2217 Alder Creek Rd. Suite 40<br>Northfield, MN 55057</p>
    <ul class="contacts">
      <li>
        <svg viewBox="0 0 24 24" aria-hidden="true"><path d="M6.6 10.8a15.1 15.1 0 0 0 6.6 6.6l2.2-2.2a1 1 0 0 1 1-.25 11.4 11.4 0 0 0 3.6.57 1 1 0 0 1 1 1V20a1 1 0 0 1-1 1A17 17 0 0 1 3 4a1 1 0 0 1 1-1h3.5a1 1 0 0 1 1 1c0 1.25.2 2.45.57 3.57a1 1 0 0 1-.25 1z"/></svg>
        555-204-8816
      </li>
      <li>
        <svg viewBox="0 0 24 24" aria-hidden="true"><path d="M2 5h20v14H2z M2 5l10 8 10-8" /></svg>
        hello@verodex-mail.com
      </li>
      <li>
        <svg viewBox="0 0 24 24" aria-hidden="true"><path d="M12 2a10 10 0 1 0 0 20 10 10 0 0 0 0-20zm6.9 6h-3a15.6 15.6 0 0 0-1.4-3.6A8 8 0 0 1 18.9 8zM12 4c.8 1.2 1.5 2.5 1.9 4h-3.8c.4-1.5 1.1-2.8 1.9-4zM4.3 14a8 8 0 0 1 0-4h3.4a16 16 0 0 0 0 4zm.8 2h3a15.6 15.6 0 0 0 1.4 3.6A8 8 0 0 1 5.1 16zm3-8h-3a8 8 0 0 1 4.4-3.6A15.6 15.6 0 0 0 8.1 8zM12 20c-.8-1.2-1.5-2.5-1.9-4h3.8c-.4 1.5-1.1 2.8-1.9 4zm2.3-6H9.7a14.6 14.6 0 0 1 0-4h4.6a14.6 14.6 0 0 1 0 4zm.2 5.6a15.6 15.6 0 0 0 1.4-3.6h3a8 8 0 0 1-4.4 3.6zm1.8-5.6a16 16 0 0 0 0-4h3.4a8 8 0 0 1 0 4z"/></svg>
        www.verodex-trade.com
      </li>
    </ul>
  </section>

  <section class="card card-back">
    <div class="brand">
      <span class="brand-mark"></span>
      <span class="brand-name">VERODEX</span>
    </div>
  </section>
</div>
</body>
</html>
```